Firm Stationery Design

I need a design for stationery, including: Stationery First Page, Stationery Second Sheet, Envelope, Mailing Label for Flat Envelopes, and Business Cards

```html
<!DOCTYPE html>
<html lang="en">
<head>
<meta charset="utf-8">
<title>Harlow Law LLC – Mailing Label</title>
<link href="https://fonts.googleapis.com/css2?family=Montserrat:wght@400;700;800&display=swap" rel="stylesheet">
<style>
  :root {
    --backdrop: #bfbfbf;
    --paper: #ffffff;
    --panel: #ededed;
    --accent: #f8a41f;
    --ink: #1c1c1c;
    --text: #333333;
  }
  * { margin: 0; padding: 0; box-sizing: border-box; }
  html, body { width: 1200px; height: 895px; overflow: hidden; }
  body {
    background: var(--backdrop);
    font-family: "Montserrat", sans-serif;
    color: var(--text);
    position: relative;
  }
  .section-tag {
    position: absolute; left: 782px; top: 15px; width: 374px; height: 104px;
    background: var(--accent); color: var(--paper);
    display: flex; align-items: center; justify-content: center;
    font-size: 35px; font-weight: 400; letter-spacing: 0.5px;
  }
  .label {
    position: absolute; background: var(--paper); overflow: hidden;
  }
  .label__panel { position: absolute; background: var(--panel); }
  .label__content { position: absolute; }
  .brand { display: flex; align-items: center; gap: 7px; }
  .brand__mark { background: var(--accent); flex: none; }
  .brand__name { font-weight: 800; color: var(--ink); white-space: nowrap; }
  .person__name { font-weight: 700; color: var(--accent); letter-spacing: 0.3px; }
  .person__role, .address, .contact { font-weight: 400; color: var(--text); }
  .contact { display: flex; align-items: center; gap: 5px; }
  .contact svg { flex: none; fill: var(--accent); }

  /* landscape label */
  .label--wide { left: 148px; top: 282px; width: 441px; height: 331px; }
  .label--wide .label__panel { left: 154px; top: 0; right: 0; bottom: 0; }
  .label--wide .label__content { left: 31px; top: 64px; }
  .label--wide .brand__mark { width: 12px; height: 12px; }
  .label--wide .brand__name { font-size: 18px; }
  .label--wide .person__name { font-size: 17px; margin-top: 43px; line-height: 20px; }
  .label--wide .person__role { font-size: 12px; line-height: 16px; }
  .label--wide .address { font-size: 11.5px; line-height: 16px; margin-top: 16px; }
  .label--wide .contacts { margin-top: 14px; }
  .label--wide .contact { font-size: 11.5px; line-height: 16px; }

  /* portrait label */
  .label--tall { left: 668px; top: 192px; width: 384px; height: 511px; }
  .label--tall .label__panel { left: 0; top: 136px; right: 0; bottom: 0; }
  .label--tall .brand-block { position: absolute; left: 46px; top: 68px; }
  .label--tall .brand__mark { width: 14px; height: 14px; }
  .label--tall .brand__name { font-size: 21px; }
  .label--tall .label__content { left: 46px; top: 147px; }
  .label--tall .person__name { font-size: 20px; line-height: 24px; }
  .label--tall .person__role { font-size: 13.5px; line-height: 18px; }
  .label--tall .address { font-size: 13.5px; line-height: 18px; margin-top: 8px; }
  .label--tall .contacts { margin-top: 8px; }
  .label--tall .contact { font-size: 14px; line-height: 18px; }
</style>
</head>
<body>
  <div class="section-tag">Mailing Label</div>

  <section class="label label--wide">
    <div class="label__panel"></div>
    <div class="label__content">
      <div class="brand"><span class="brand__mark"></span><span class="brand__name">HARLOW LAW LLC</span></div>
      <p class="person__name">DANIEL REED</p>
      <p class="person__role">Managing Director</p>
      <p class="address">Your address, City<br>State, Zip 1234</p>
      <div class="contacts">
        <p class="contact"><svg width="9" height="9" viewBox="0 0 10 10"><path d="M1 4c0-2 8-2 8 0v1H7V4H3v1H1z M2 6h6l1 3H1z"/></svg>123 456 789</p>
        <p class="contact"><svg width="9" height="9" viewBox="0 0 10 10"><path d="M0 2h10v1L5 6 0 3z M0 4l5 3 5-3v4H0z"/></svg>info@harlowlawllc.com</p>
        <p class="contact"><svg width="9" height="9" viewBox="0 0 10 10"><circle cx="5" cy="5" r="4.5"/></svg>www.harlowlawllc.com</p>
      </div>
    </div>
  </section>

  <section class="label label--tall">
    <div class="label__panel"></div>
    <div class="brand-block">
      <div class="brand"><span class="brand__mark"></span><span class="brand__name">HARLOW LAW LLC</span></div>
    </div>
    <div class="label__content">
      <p class="person__name">DANIEL REED</p>
      <p class="person__role">Managing Director</p>
      <p class="address">Your address, City<br>State, Zip 1234</p>
      <div class="contacts">
        <p class="contact"><svg width="10" height="10" viewBox="0 0 10 10"><path d="M1 4c0-2 8-2 8 0v1H7V4H3v1H1z M2 6h6l1 3H1z"/></svg>123 456 789</p>
        <p class="contact"><svg width="10" height="10" viewBox="0 0 10 10"><path d="M0 2h10v1L5 6 0 3z M0 4l5 3 5-3v4H0z"/></svg>info@harlowlawllc.com</p>
        <p class="contact"><svg width="10" height="10" viewBox="0 0 10 10"><circle cx="5" cy="5" r="4.5"/></svg>www.harlowlawllc.com</p>
      </div>
    </div>
  </section>
</body>
</html>
```